Business cards to launch an education platform

Hi,
I am looking at having new business cards designed.
I am a startup, developing a web platform for schools and university, the education world. It's an online assessment system.
I would like a card that looks classy, and that is using the colors and the font of my logo.

I have attached:
1) my logo
2) A business card that I have designed quickly so you can have all the information required in the card, but I really don't like it.
3) The font that I am using (Lato Regular) to design my web platform
4) Some screenshots of my web platform so you can have a look at the style that I have.

Target Market(s)

Major market: Education system: Schools and university
Minor markets: Business in general

Industry/Entity Type

Business

Contact Information for Business Card

Clara Fenwick
Director

M: 0437 518 902
E: clara.fenwick@amberLoomSystems.com.au

Requirements
Must have
• The colors of my logo

```html
<!DOCTYPE html>
<html lang="en">
<head>
<meta charset="utf-8">
<title>Amber Loom Systems – Business Cards</title>
<link rel="stylesheet" href="https://fonts.googleapis.com/css2?family=Lato:wght@400;700&family=Roboto+Condensed:wght@300;400;500&display=swap">
<style>
  :root {
    --page-bg: #e4e5e7;
    --card-light: #f2f2f3;
    --navy: #0b3a69;
    --navy-deep: #073360;
    --ink: #1f3858;
    --sky: #2d9fd6;
    --white: #ffffff;
  }
  * { box-sizing: border-box; margin: 0; padding: 0; }
  html, body {
    width: 1105px;
    height: 1200px;
    overflow: hidden;
    background: var(--page-bg);
  }
  .canvas {
    position: relative;
    width: 1105px;
    height: 1200px;
  }
  .card {
    position: absolute;
    left: 102px;
    width: 900px;
    height: 512px;
    overflow: hidden;
  }
  .card--front { top: 60px; background: var(--card-light); }
  .card--back { top: 628px; background: var(--navy-deep); }

  /* Front */
  .name-band {
    position: absolute;
    left: 0;
    top: 55px;
    width: 520px;
    height: 146px;
    background: var(--navy);
    clip-path: polygon(0 0, 100% 0, 88% 100%, 0 100%);
  }
  .holder-name {
    position: absolute;
    left: 60px;
    top: 78px;
    font-family: "Roboto Condensed", sans-serif;
    font-weight: 500;
    font-size: 43px;
    color: var(--white);
  }
  .holder-role {
    position: absolute;
    left: 60px;
    top: 134px;
    font-family: "Roboto Condensed", sans-serif;
    font-weight: 500;
    font-size: 30px;
    color: var(--white);
  }
  .brand {
    position: absolute;
    display: flex;
    align-items: center;
    gap: 20px;
  }
  .brand--front { left: 540px; top: 78px; }
  .brand-square {
    width: 76px;
    height: 76px;
    background: var(--sky);
  }
  .brand-name {
    font-family: "Lato", sans-serif;
    font-weight: 400;
    font-size: 31px;
    line-height: 1.15;
    letter-spacing: 2px;
    color: var(--ink);
  }
  .contact-list {
    position: absolute;
    left: 66px;
    top: 358px;
    list-style: none;
  }
  .contact-item {
    display: flex;
    align-items: center;
    gap: 16px;
    height: 35px;
    font-family: "Roboto Condensed", sans-serif;
    font-weight: 300;
    font-size: 21px;
    color: var(--ink);
  }
  .contact-icon { width: 22px; height: 22px; flex: none; }

  /* Back */
  .brand-block {
    position: absolute;
    left: 68px;
    top: 330px;
  }
  .brand-name--back {
    font-family: "Lato", sans-serif;
    font-weight: 400;
    font-size: 48px;
    line-height: 1.1;
    letter-spacing: 4px;
    color: var(--white);
  }
  .brand-web {
    margin-top: 8px;
    font-family: "Lato", sans-serif;
    font-size: 25px;
    color: var(--white);
  }
  .brand-square--large {
    position: absolute;
    left: 540px;
    top: 110px;
    width: 290px;
    height: 290px;
    background: linear-gradient(135deg, #1f6fb4, #2aa8dc);
  }
</style>
</head>
<body>
<main class="canvas">

  <section class="card card--front" aria-label="Business card front">
    <div class="name-band"></div>
    <h1 class="holder-name">Clara Fenwick</h1>
    <p class="holder-role">Director</p>

    <div class="brand brand--front">
      <span class="brand-square"></span>
      <p class="brand-name">AMBER LOOM<br>SYSTEMS</p>
    </div>

    <ul class="contact-list">
      <li class="contact-item">
        <svg class="contact-icon" viewBox="0 0 22 22" aria-hidden="true">
          <rect x="6" y="1" width="10" height="20" rx="2" fill="none" stroke="#1f3858" stroke-width="2"/>
          <rect x="8" y="4" width="6" height="12" fill="#1f3858"/>
        </svg>
        <span>0437 518 902</span>
      </li>
      <li class="contact-item">
        <svg class="contact-icon" viewBox="0 0 22 22" aria-hidden="true">
          <rect x="2" y="5" width="18" height="12" fill="#1f3858"/>
          <path d="M2 5 L11 12 L20 5" fill="none" stroke="#f2f2f3" stroke-width="1.5"/>
        </svg>
        <span>clara.fenwick@amberLoomSystems.com.au</span>
      </li>
      <li class="contact-item">
        <svg class="contact-icon" viewBox="0 0 22 22" aria-hidden="true">
          <circle cx="11" cy="11" r="9" fill="#1f3858"/>
          <path d="M2 11 H20 M11 2 C6 7 6 15 11 20 M11 2 C16 7 16 15 11 20" fill="none" stroke="#f2f2f3" stroke-width="1.2"/>
        </svg>
        <span>www.amberLoomSystems.com.au</span>
      </li>
    </ul>
  </section>

  <section class="card card--back" aria-label="Business card back">
    <span class="brand-square--large"></span>
    <div class="brand-block">
      <p class="brand-name--back">AMBER LOOM<br>SYSTEMS</p>
      <p class="brand-web">amberLoomSystems.com.au</p>
    </div>
  </section>

</main>
</body>
</html>
```